American cannabis tech company business card design

Pavrel.com is seeking a modern, professional, and brand-aligned business card that represents our company and its core values: Mission, Story, Values, and Impact. As an innovative cannabis company, we want a business card that is not only visually appealing but also serves as a representation of who we are and what we stand for.

Project Scope: Design a double-sided business card that integrates our brand identity and core values. Incorporate our key brand elements, ensuring a sleek and contemporary aesthetic. Visually reflect our core values (Mission, Story, Values, Impact) in a way that is engaging yet professional.

Target Market(s)

Vendors, third parties,

Contact Information for Business Card

Contact details (name, title, email, phone, website, etc.)

Font styles to use
Other font styles liked:
• Caslon, Centra

Colors

Designer to choose colors to be used in the design.

Requirements
Must have
• Pavrel.com logo and branding A creative yet clean way to integrate our core values (Mission, Story, Values, Impact) Modern typography and a well-structured layout
Nice to have
• forest green, grey, white, black
Should not have
• references to marijuana, leafs, plants, or related product

```html
<!DOCTYPE html>
<html lang="en">
<head>
<meta charset="utf-8">
<title>Pavrel Business Card</title>
<link href="https://fonts.googleapis.com/css2?family=Montserrat:wght@400;500;700;800&display=swap" rel="stylesheet">
<style>
  :root {
    --forest: #1a3320;
    --forest-deep: #173b22;
    --forest-mark: #21442a;
    --paper: #ffffff;
    --ink: #1b1b1b;
    --backdrop: #e6e8e6;
  }
  * { margin: 0; padding: 0; box-sizing: border-box; }
  html, body {
    width: 1200px; height: 900px; overflow: hidden;
    background: var(--backdrop);
    font-family: "Montserrat", sans-serif;
  }
  .canvas { position: relative; width: 1200px; height: 900px; }
  .card {
    position: absolute; left: 260px;
    width: 680px; height: 388px;
    border-radius: 26px;
    overflow: hidden;
    box-shadow: 0 6px 18px rgba(0,0,0,.15);
  }
  .card-back { top: 40px; background: var(--forest); display: flex; align-items: center; justify-content: center; }
  .card-back .wordmark { color: var(--forest-mark); font-size: 112px; font-weight: 800; letter-spacing: 2px; }
  .card-front { top: 472px; background: var(--paper); }
  .card-front .wordmark {
    position: absolute; left: 40px; top: 26px;
    color: var(--forest-deep); font-size: 84px; font-weight: 800; letter-spacing: 1px;
  }
  .person { position: absolute; left: 40px; top: 170px; }
  .person .name { color: var(--forest-deep); font-size: 26px; font-weight: 700; }
  .person .title { color: var(--ink); font-size: 15px; font-weight: 400; margin-top: 2px; }
  .divider { position: absolute; left: 40px; right: 70px; top: 238px; height: 2px; background: var(--ink); }
  .contacts { position: absolute; left: 40px; top: 252px; list-style: none; }
  .contacts li { display: flex; align-items: center; gap: 12px; font-size: 15px; color: var(--ink); line-height: 26px; }
  .contacts svg { width: 13px; height: 13px; fill: var(--forest-deep); }
  .address {
    position: absolute; right: 90px; bottom: 40px;
    font-size: 15px; color: var(--ink); line-height: 22px;
  }
</style>
</head>
<body>
<div class="canvas">
  <section class="card card-back">
    <span class="wordmark">PAVREL</span>
  </section>

  <section class="card card-front">
    <span class="wordmark">PAVREL</span>
    <div class="person">
      <p class="name">Daniel Marsh</p>
      <p class="title">Co-Founder &amp; CEO</p>
    </div>
    <div class="divider"></div>
    <ul class="contacts">
      <li>
        <svg viewBox="0 0 16 16" aria-hidden="true"><path d="M3 1h3l1.5 4-2 1.2a9 9 0 0 0 4.3 4.3L11 8.5l4 1.5v3a2 2 0 0 1-2 2A12 12 0 0 1 1 3a2 2 0 0 1 2-2z"/></svg>
        +1 405-555-0148
      </li>
      <li>
        <svg viewBox="0 0 16 16" aria-hidden="true"><path d="M1 3h14v10H1z M1 3l7 6 7-6" /></svg>
        team@pavrel.com
      </li>
      <li>
        <svg viewBox="0 0 16 16" aria-hidden="true"><circle cx="8" cy="8" r="7"/></svg>
        www.pavrel.com
      </li>
    </ul>
    <address class="address" style="font-style:normal">
      1180 Birch Avenue<br>Dallas, TX 75204
    </address>
  </section>
</div>
</body>
</html>
```